Business Cards for new orthopaedic surgery practice

My husband and I are starting our own orthopaedic surgery practice. We are looking for a business card that is uniform, but one will have my name/title and the other will have his. You can just create one design with my name on it for now. But when I choose your design as the winning design I will ask that you add another copy with his name/title.

We are looking for classy, simple, elite all in one. We like dark blues/a little gold/yellow. Something that goes with our logo. We want our logo incorporated. Here is all the info you need:
Business name: RV Bone & Vitality Center
Location: 38517 North Willowmere Ave
Palm Hollow, FL 34990
Phone: 954-218-4063
Fax: 954-582-7341
Email: info@myrvbonecare.example

Names: Lydia Vance, M.D.
Board Certified Hand and Upper Extremity Surgeon

Ebo Dansu, M.D.
Board Certified Hip & Knee Replacement/General Orthopaedic Surgeon

Can decide what you want to put on the back. Maybe a slogan:
Rooted in Care. Focused on You

I am just going to upload our logo. The only thing is if we select you as the winning design, the location, and phone numbers may change. We will need your help to update that once fully solidified.

Industry/Entity Type

Medical

Contact Information for Business Card

Colors
0054AA
0677BA
7BADD7
CADEEF
E8F1F8
0094D4
00A9DD
6FCCEA
C7EBF8
E9F6FB

Requirements
Must have
• class, appeal,
Should not have
• We want to air on the side of masculine if we are looking at masculine vs. feminine feel. But we still want it classy, sophisticated, and something we will love

```html
<!DOCTYPE html>
<html lang="en">
<head>
<meta charset="utf-8">
<title>RV Bone &amp; Vitality Center – Business Card</title>
<link rel="stylesheet" href="https://fonts.googleapis.com/css2?family=Inter:wght@600&family=Tinos:wght@400;700&display=swap">
<style>
  :root {
    --backdrop: #959595;
    --paper: #ffffff;
    --navy: #1b2a4e;
    --gold: #d4b27a;
    --mark: #e6e6e6;
  }
  * { box-sizing: border-box; margin: 0; padding: 0; }
  html, body { width: 1200px; height: 579px; overflow: hidden; }
  body {
    background: var(--backdrop);
    font-family: "Tinos", "Times New Roman", serif;
    color: var(--navy);
    display: flex;
    justify-content: center;
    align-items: center;
    gap: 20px;
  }
  .side { width: 550px; }
  .side-label {
    font-family: "Inter", Arial, sans-serif;
    font-weight: 600;
    font-size: 17px;
    color: #fff;
    margin: 0 0 6px 10px;
  }
  .trim-sheet { position: relative; width: 550px; height: 359px; }
  .crop-marks { position: absolute; inset: 0; }
  .crop-marks line { stroke: var(--mark); stroke-width: 1; }
  .card {
    position: absolute;
    left: 40px; top: 40px;
    width: 470px; height: 279px;
    background: var(--paper);
    overflow: hidden;
  }
  .holder-name {
    position: absolute; left: 48px; top: 56px;
    font-weight: 700; font-size: 18px; letter-spacing: -0.1px;
  }
  .holder-title {
    position: absolute; left: 48px; top: 78px;
    font-weight: 700; font-size: 9.6px;
  }
  .gold-rule {
    position: absolute; left: 49px; top: 114px;
    width: 185px; height: 1px; background: var(--gold);
  }
  .contact-list {
    position: absolute; left: 49px; top: 149px;
    font-size: 9.8px;
    display: grid; grid-template-columns: 44px auto;
    row-gap: 6px; line-height: 1.25;
  }
  .contact-list dt { font-weight: 700; }
  .contact-list dd { font-weight: 700; }
  .contact-list .phone-row { margin-top: 12px; }
  .accent-band {
    position: absolute; left: 331px; top: 0;
    width: 87px; height: 100%;
    background: var(--navy);
  }
  .practice-seal {
    position: absolute; left: 322px; top: 86px;
    width: 104px; height: 104px; border-radius: 50%;
    background: var(--paper);
    display: flex; align-items: center; justify-content: center;
    text-align: center;
  }
  .practice-name {
    font-weight: 700; font-size: 12px; line-height: 1.2;
    color: var(--navy); letter-spacing: 0.5px;
  }
  .practice-seal.is-large {
    left: 150px; top: 55px; width: 170px; height: 170px;
    border: 1.5px solid var(--navy);
  }
  .practice-seal.is-large .practice-name { font-size: 19px; letter-spacing: 0.8px; }
</style>
</head>
<body>

  <section class="side side-front">
    <p class="side-label">Front</p>
    <div class="trim-sheet">
      <svg class="crop-marks" width="550" height="359" aria-hidden="true">
        <line x1="4" y1="52" x2="40" y2="52"/><line x1="52" y1="4" x2="52" y2="40"/>
        <line x1="510" y1="52" x2="546" y2="52"/><line x1="498" y1="4" x2="498" y2="40"/>
        <line x1="4" y1="307" x2="40" y2="307"/><line x1="52" y1="319" x2="52" y2="355"/>
        <line x1="510" y1="307" x2="546" y2="307"/><line x1="498" y1="319" x2="498" y2="355"/>
      </svg>
      <article class="card card-front">
        <h1 class="holder-name">Lydia Vance, M.D.</h1>
        <p class="holder-title">Board Certified Hand and Upper Extremity Surgeon</p>
        <div class="gold-rule"></div>
        <dl class="contact-list">
          <dt>Address</dt><dd>: 38517 North Willowmere Ave<br>&nbsp;&nbsp;Palm Hollow, FL 34990</dd>
          <dt class="phone-row">Phone</dt><dd class="phone-row">: 954-218-4063</dd>
          <dt>Fax</dt><dd>: 954-582-7341</dd>
          <dt>Email</dt><dd>: info@myrvbonecare.example</dd>
        </dl>
        <div class="accent-band"></div>
        <div class="practice-seal">
          <span class="practice-name">RV Bone &amp;<br>Vitality<br>Center</span>
        </div>
      </article>
    </div>
  </section>

  <section class="side side-back">
    <p class="side-label">Back</p>
    <div class="trim-sheet">
      <svg class="crop-marks" width="550" height="359" aria-hidden="true">
        <line x1="4" y1="52" x2="40" y2="52"/><line x1="52" y1="4" x2="52" y2="40"/>
        <line x1="510" y1="52" x2="546" y2="52"/><line x1="498" y1="4" x2="498" y2="40"/>
        <line x1="4" y1="307" x2="40" y2="307"/><line x1="52" y1="319" x2="52" y2="355"/>
        <line x1="510" y1="307" x2="546" y2="307"/><line x1="498" y1="319" x2="498" y2="355"/>
      </svg>
      <article class="card card-back">
        <div class="practice-seal is-large">
          <span class="practice-name">RV Bone &amp;<br>Vitality<br>Center</span>
        </div>
      </article>
    </div>
  </section>

</body>
</html>
```